Manuka Honey company needs a Upmarket, Luxury Website!

New Zealand, Taranaki based Manuka Honey company Rimu Vale Honey is looking for a new website, we are looking for an upmarket, luxury, serious website design. We export the highest quality quality Manuka Honey, straight from the Taranaki region.

Main export markets are Asia & Europe, also New Zealand & Australia.

Looking to have a beautiful, upmarket, serious, luxurious & graphical experience with mobile optimization in mind. Like the use of product staging/mockups

You can use copy from other websites to build the site and we will change the copy after the design is finished.

***Please include 'Honey Product' mockups in website.

*Will add illustrator files in coming days***

Feel free to make website functional in Shopify, Wordpress or WIX

Target Market(s)

Asia, Europe (main markets) New Zealand, Australia (Submarkets)

Coding

Coded - Design and coding required

Number of Pages Required

4 page

Requirements
Must have
• Home, Shop, About Us, Contact Us

Homepage to include:

Our Products
Company Video (video under construction)
What is MGO/KPS
Newsletter Opt-in

***(Not in Order)***

Please include 'Honey Product' mockups in website.
*Will add illustrator files in coming days
Nice to have
• FAQ & Partnership Inquiries (hyperlink in footer)

```html
<!DOCTYPE html>
<html lang="en">
<head>
<meta charset="utf-8">
<title>Rimu Vale Honey — Manuka Honey</title>
<link href="https://fonts.googleapis.com/css2?family=Montserrat:wght@400;500;600;700;800&display=swap" rel="stylesheet">
<style>
:root{
  --gold:#f9ab00;
  --gold-deep:#d99400;
  --gold-text:#e0a100;
  --ink:#1f1f1f;
  --body:#4a4a4a;
  --paper:#ece9e3;
  --cream:#f2e4ba;
  --dark:#2a2a2a;
  --white:#ffffff;
}
*{margin:0;padding:0;box-sizing:border-box}
html,body{width:1200px;height:4367px;overflow:hidden}
body{font-family:"Montserrat",sans-serif;color:var(--body);background:var(--white);position:relative}
section,header,footer{position:absolute;left:0;width:1200px}
.abs{position:absolute}
.btn{position:absolute;background:var(--gold);color:var(--ink);font-weight:700;text-transform:uppercase;display:flex;align-items:center;justify-content:center}
.squiggle{position:absolute;left:50%;transform:translateX(-50%)}
.section-title{position:absolute;left:0;width:100%;text-align:center;color:var(--gold-text);font-weight:700;font-size:30px}

/* header + hero */
.hero{top:0;height:776px;background:linear-gradient(90deg,#fbe3a2 0%,#fff6dc 22%,#fff 34%)}
.brand{top:56px;left:85px;display:flex;align-items:center;gap:12px}
.brand-mark{width:42px;height:42px;border-radius:50%;background:var(--gold)}
.brand-name{font-size:25px;letter-spacing:3px;color:var(--ink);font-weight:500}
.nav{top:66px;left:548px;display:flex;gap:0;font-size:11.5px;color:var(--ink);font-weight:500}
.nav a{color:inherit;text-decoration:none;margin-right:30px}
.nav a.active{color:var(--gold-text)}
.cart{top:60px;left:957px}
.shop-top{top:59px;left:1023px;width:84px;height:24px;font-size:10.5px}
.eyebrow{top:374px;left:90px;font-size:12.5px;color:var(--gold-deep);font-weight:600}
.hero-title{top:392px;left:88px;font-size:66px;font-weight:800;color:var(--ink);letter-spacing:-1px}
.hero-copy{top:476px;left:90px;width:510px;font-size:13px;line-height:17px;color:#333}
.shop-now{top:576px;left:90px;width:130px;height:41px;font-size:12px;border-radius:2px}
.hero-arrow{top:583px;left:40px}
.hero-art{left:492px;top:270px;width:652px;height:460px;border-radius:46% 42% 38% 50%;background:radial-gradient(circle at 55% 55%,#f5a300 0%,#f7c24a 38%,#fde9b5 62%,rgba(255,255,255,0) 75%)}

/* about */
.about{top:776px;height:461px;background:var(--gold)}
.about-photo{left:86px;top:75px;width:487px;height:325px;background:linear-gradient(120deg,#b65b12 0%,#e59a2c 35%,#f3d5d6 60%,#e8a5c8 100%)}
.about-eyebrow{left:636px;top:93px;font-size:10px;font-weight:600;color:#333;letter-spacing:1px}
.about-title{left:636px;top:108px;font-size:36px;font-weight:700;color:var(--ink)}
.about-copy{left:645px;top:218px;width:420px;font-size:12.5px;line-height:16.5px;color:#3a2a00;text-align:justify}
.about-copy p{margin-bottom:16px}

/* products */
.products{top:1237px;height:763px;background:var(--paper)}
.card{position:absolute;top:214px;width:212px;height:380px;background:var(--white)}
.card-img{height:212px;background:#eeeeee;display:flex;align-items:center;justify-content:center}
.card-img span{display:block;width:130px;height:110px;border-radius:45%;background:radial-gradient(circle,#f6a400 0%,#f8c453 55%,rgba(238,238,238,0) 72%)}
.stars{position:absolute;left:16px;top:232px;display:flex;gap:2px}
.stars i{width:7px;height:7px;border:1px solid #f3b63a;border-radius:50%}
.card-name{position:absolute;left:16px;top:256px;font-size:12px;color:#333}
.card-price{position:absolute;left:16px;top:290px;font-size:12.5px;font-weight:600;color:var(--ink)}
.add-cart{position:absolute;left:16px;top:320px;width:144px;height:33px;border-radius:17px;background:#333;color:#fff;font-size:11px;font-weight:600;display:flex;align-items:center;justify-content:center}
.more-dot{position:absolute;left:168px;top:322px;width:29px;height:29px;border-radius:50%;background:#e6e6e6;display:flex;align-items:center;justify-content:center;gap:2px}
.more-dot i{width:3px;height:3px;border-radius:50%;background:#555}
.more-product{left:547px;top:643px;width:116px;height:30px;font-size:12px;color:#fff;text-transform:none}

/* testimonials */
.reviews{top:2000px;height:415px;background:radial-gradient(ellipse at 55% 45%,#3b3a2c 0%,#262519 60%,#1b1b14 100%)}
.review-text{left:240px;top:222px;width:720px;text-align:center;font-size:12px;line-height:16px;color:#fff}
.review-name{left:0;width:100%;top:292px;text-align:center;color:var(--gold);font-weight:700;font-size:13px}
.review-role{left:0;width:100%;top:310px;text-align:center;color:#fff;font-size:11px}
.round-arrow{position:absolute;top:237px;width:30px;height:30px;border-radius:50%;background:var(--gold-deep)}

/* blog */
.blog{top:2415px;height:717px;background:var(--white)}
.post{position:absolute;top:214px;width:504px;text-align:center}
.post-img{height:334px}
.tag{position:absolute;top:321px;left:50%;transform:translateX(-50%);background:var(--gold);color:#fff;font-size:12px;font-weight:600;padding:5px 11px}
.post-title{margin-top:17px;font-size:14px;font-weight:700;color:var(--ink)}
.post-meta{margin-top:6px;font-size:10px;color:#555}
.read-more{margin-top:25px;font-size:12px;font-weight:600;color:var(--gold-text)}

/* faq */
.faq{top:3132px;height:526px;background:var(--cream)}
.faq-item{position:absolute;left:136px;width:393px;height:47px;border:1.5px solid var(--gold);display:flex;align-items:center;padding-left:24px;font-size:11.5px;color:#444}
.faq-item b{position:absolute;right:10px;top:10px;color:var(--gold);font-size:22px;font-weight:400}
.faq-open{left:575px;top:177px;width:544px;height:269px;background:var(--gold);border:2px solid #e89c00;padding:30px 36px;color:#fff}
.faq-open h3{font-size:11.5px;font-weight:500;display:flex;justify-content:space-between}
.faq-open p{margin-top:20px;font-size:11.5px;line-height:13.5px;text-align:justify}

/* newsletter + contact */
.connect{top:3658px;height:325px;background:var(--white)}
.col-title{position:absolute;width:560px;text-align:center;color:var(--gold-text);font-size:30px;font-weight:600}
.col-copy{position:absolute;width:560px;text-align:center;font-size:11px;line-height:14px;color:#444}
.email{left:151px;top:198px;width:262px;height:36px;border:1.5px solid var(--gold);font-size:10.5px;font-style:italic;color:#999;display:flex;align-items:center;padding-left:10px}
.subscribe{left:413px;top:198px;width:136px;height:36px;font-size:10.5px;color:#fff}
.social{position:absolute;top:226px;left:830px;display:flex;gap:5px}
.social i{width:24px;height:24px;border-radius:50%;border:2px solid var(--gold)}
.social i:nth-child(n+3){background:var(--gold)}

/* footer */
.footer{top:3983px;height:322px;background:var(--dark);color:#ddd}
.foot-brand{left:115px;top:90px;display:flex;align-items:center;gap:8px}
.foot-brand .brand-mark{width:34px;height:34px}
.foot-brand .brand-name{color:var(--gold);font-size:19px}
.foot-about{left:118px;top:142px;width:206px;font-size:10.5px;line-height:13.5px;text-align:justify;color:#ddd}
.foot-btn{left:118px;top:225px;width:100px;height:28px;font-size:8px;color:#fff}
.foot-head{position:absolute;top:82px;color:var(--gold);font-size:16px;font-weight:700;text-decoration:underline;text-underline-offset:4px}
.foot-rule{position:absolute;top:100px;width:1px;height:180px;background:#555}
.foot-list{position:absolute;top:127px;list-style:none;font-size:13px;line-height:24px}
.foot-list li::before{content:"•";color:var(--gold);margin-right:10px}
.foot-contact{position:absolute;left:578px;top:122px;font-size:13px;line-height:17px}
.foot-contact div{display:flex;gap:10px;margin-bottom:6px}
.foot-contact svg{flex:none;margin-top:2px}
.foot-post{position:absolute;left:835px;display:flex;gap:12px}
.foot-post .thumb{width:62px;height:42px;background:linear-gradient(135deg,#f0b13a,#c9731b)}
.foot-post h4{font-size:13px;line-height:16px;color:#fff;font-weight:600}
.foot-post small{display:block;font-size:8px;color:#fff;margin-top:4px}
.copyright{top:4305px;height:62px;background:linear-gradient(90deg,#f2c34b 0%,#f7b100 50%,#f2c34b 100%);display:flex;align-items:center;padding-left:112px;font-size:12px;color:#222}
.mini-social{position:absolute;right:120px;top:25px;display:flex;gap:22px}
.mini-social i{width:9px;height:9px;background:#333}
</style>
</head>
<body>

<header class="hero">
  <div class="abs hero-art" role="img" aria-label="Honey jar, wooden spoon, honeycomb and manuka blossom"></div>
  <div class="abs brand"><span class="brand-mark"></span><span class="brand-name">RIMU VALE HONEY</span></div>
  <nav class="abs nav"><a class="active">Home</a><a>Shop</a><a>About Us</a><a>Products</a><a>Blog</a><a>Contact Us</a></nav>
  <svg class="abs cart" width="26" height="24" viewBox="0 0 26 24" fill="none" stroke="#e0a100" stroke-width="2"><path d="M1 2h4l3 13h13l3-9H7"/><circle cx="10" cy="20" r="2"/><circle cx="19" cy="20" r="2"/></svg>
  <div class="btn shop-top">Shop Now</div>
  <div class="abs eyebrow">WELCOME TO RIMU VALE HONEY CO</div>
  <h1 class="abs hero-title">MANUKA HONEY</h1>
  <p class="abs hero-copy">Nam quibus rebus efficiuntur voluptates, eae non sunt in potestate sapientis. Negare non possum. Huic mori optimum esse propter desperationem sapientiae, illi propter spem vivere. Quid enim me prohiberet</p>
  <div class="btn shop-now">Shop Now</div>
  <svg class="abs hero-arrow" width="22" height="40" viewBox="0 0 22 40" fill="none" stroke="#fff" stroke-width="2"><path d="M20 2 3 20l17 18"/></svg>
</header>

<section class="about">
  <div class="abs about-photo" role="img" aria-label="Bowl of honey with a dipper beside manuka flowers"></div>
  <div class="abs about-eyebrow">ABOUT US</div>
  <h2 class="abs about-title">Welcome to Rimu Vale Honey</h2>
  <svg class="abs" style="left:650px;top:166px" width="140" height="20" viewBox="0 0 140 20" fill="none" stroke="#333" stroke-dasharray="2 3"><path d="M2 14c30-8 60 8 95-4 12-4 20-6 30-6"/></svg>
  <div class="abs about-copy">
    <p>constructio interrete. Quia nec honesto quic quam honestius nec turpi turpius. Tria genera bonorum; Quid iudicant sensus? Quae qual non vident, nihil umquam magnum ac cognitione</p>
    <p>dignum amaverunt. Dicet pro me ipsa virtus nec dubitabit isti vestro beato M. Nihil ad rem! Ne sit sane; Nihil ad rem! Ne sit sane; Philosophi autem in suis lectulis plerumque</p>
    <p>moriuntur. Paulum, cum regem Persem captum adduceret, eodem flumine invectio?</p>
  </div>
</section>

<section class="products">
  <h2 class="section-title" style="top:80px">Our Product</h2>
  <svg class="squiggle" style="top:122px" width="140" height="20" viewBox="0 0 140 20" fill="none" stroke="#333" stroke-dasharray="2 3"><path d="M2 10c30-8 60 10 95 2 12-3 20-5 30-5"/></svg>
  <svg class="abs" style="left:56px;top:360px" width="26" height="50" viewBox="0 0 26 50" fill="none" stroke="#bbb" stroke-width="2"><path d="M24 2 3 25l21 23"/></svg>
  <svg class="abs" style="left:1120px;top:360px" width="26" height="50" viewBox="0 0 26 50" fill="none" stroke="#bbb" stroke-width="2"><path d="M2 2l21 23L2 48"/></svg>

  <div class="card" style="left:119px"><div class="card-img" role="img" aria-label="Honeycomb pieces"><span></span></div><div class="stars"><i></i><i></i><i></i><i></i><i></i></div><div class="card-name">Autem iniurosque fortunoe</div><div class="card-price">$23.90</div><div class="add-cart">ADD TO CART</div><div class="more-dot"><i></i><i></i><i></i></div></div>
  <div class="card" style="left:373px"><div class="card-img" role="img" aria-label="Two jars of honey"><span></span></div><div class="stars"><i></i><i></i><i></i><i></i><i></i></div><div class="card-name">Autem iniurosque fortunoe</div><div class="card-price">$23.90</div><div class="add-cart">ADD TO CART</div><div class="more-dot"><i></i><i></i><i></i></div></div>
  <div class="card" style="left:627px"><div class="card-img" role="img" aria-label="Wooden spoon with honey and comb"><span></span></div><div class="stars"><i></i><i></i><i></i><i></i><i></i></div><div class="card-name">Autem iniurosque fortunoe</div><div class="card-price">$23.90</div><div class="add-cart">ADD TO CART</div><div class="more-dot"><i></i><i></i><i></i></div></div>
  <div class="card" style="left:868px"><div class="card-img" role="img" aria-label="Small honey jar with cloth lid"><span></span></div><div class="stars"><i></i><i></i><i></i><i></i><i></i></div><div class="card-name">Autem iniurosque fortunoe</div><div class="card-price">$23.90</div><div class="add-cart">ADD TO CART</div><div class="more-dot"><i></i><i></i><i></i></div></div>

  <div class="btn more-product">More Product</div>
</section>

<section class="reviews" role="img" aria-label="Dark close-up photograph of a bee on a branch">
  <h2 class="section-title" style="top:128px;color:var(--gold);font-size:27px">What Our Clients Say</h2>
  <svg class="squiggle" style="top:168px" width="140" height="20" viewBox="0 0 140 20" fill="none" stroke="#ccc" stroke-dasharray="2 3"><path d="M2 10c30-8 60 10 95 2 12-3 20-5 30-5"/></svg>
  <p class="abs review-text">Lorem ipsum dolor sit amet, consectetur adipiscing elit. Quid autem habent admirationis, cum prope accesserisusque quaque, aliter in vita? consectetur adipiscing elit. Quid autem habent admirationis, cum prope accesseris? An hoc usque quaque, aliter in vita?</p>
  <div class="abs review-name">AROHA</div>
  <div class="abs review-role">Manager</div>
  <div class="round-arrow" style="left:83px"><svg width="30" height="30" viewBox="0 0 30 30" fill="none" stroke="#222" stroke-width="3"><path d="M17 9l-6 6 6 6"/></svg></div>
  <div class="round-arrow" style="left:1078px"><svg width="30" height="30" viewBox="0 0 30 30" fill="none" stroke="#222" stroke-width="3"><path d="M13 9l6 6-6 6"/></svg></div>
</section>

<section class="blog">
  <h2 class="section-title" style="top:76px">Lates blog</h2>
  <svg class="squiggle" style="top:122px" width="140" height="20" viewBox="0 0 140 20" fill="none" stroke="#333" stroke-dasharray="2 3"><path d="M2 10c30-8 60 10 95 2 12-3 20-5 30-5"/></svg>
  <article class="post" style="left:83px">
    <div class="post-img" role="img" aria-label="Spa scene with honey treatment products" style="background:linear-gradient(120deg,#e8e4dd,#c9b79a 60%,#f2efe9)"></div>
    <span class="tag">Fashion</span>
    <h3 class="post-title">Verum tamen cum de rebus grandior</h3>
    <div class="post-meta">By Admin | 4 January 2021</div>
    <div class="read-more">READ MORE.....</div>
  </article>
  <article class="post" style="left:608px">
    <div class="post-img" role="img" aria-label="Honey dipper over a glass cup of tea" style="background:linear-gradient(120deg,#d9d6d0,#e9c276 50%,#f1efeb)"></div>
    <span class="tag">Fashion</span>
    <h3 class="post-title">Verum tamen cum de rebus grandior</h3>
    <div class="post-meta">By Admin | 4 January 2021</div>
    <div class="read-more">READ MORE.....</div>
  </article>
</section>

<section class="faq">
  <h2 class="section-title" style="top:72px">FAQS</h2>
  <svg class="squiggle" style="left:622px;top:118px" width="140" height="20" viewBox="0 0 140 20" fill="none" stroke="#333" stroke-dasharray="2 3"><path d="M2 10c30-8 60 10 95 2 12-3 20-5 30-5"/></svg>
  <div class="faq-item" style="top:178px">1 NAM QUIBUS REBUS EFFICIUNTUR VOLUPTATES?<b>+</b></div>
  <div class="faq-item" style="top:252px">2 HUIC MORI OPTIMUM ESSE PROPTER DESPERATI ?<b>+</b></div>
  <div class="faq-item" style="top:326px">3 EST ENIM EFFECTRIX MULTARUM ET MAGNARUM ?<b>+</b></div>
  <div class="faq-item" style="top:397px">4 DEQUE HIS REBUS SATIS MULTA IN NOSTRIS DE ?<b>+</b></div>
  <div class="abs faq-open">
    <h3><span>Q: STOICORUM MORE NOS SIMPLY TEXT?</span><span>–</span></h3>
    <p>Adipiscing elit. Quid autem habent admirationis, cum prope accesseris n hoc usque quaque, aliter in vita? Non igitur de improbo, sed de callido improbo quaeri-mus, qualis Q. Nam quibus rebus efficiunturvoluptates, eae non sunt in potestate sapientis. Negare non possum. Huic mori optimum esse propter desperationem sapientiae, illi propter spem vivere.<br>Et quod est munus, quod opus sapientiae? Non modo carum sibi quemque, verum etiam vehementer carum esse? Tu enim ista lenius, hic Stoicorum more nos vexat. Collatio igitur ista te nihil iuvat. Videamus animi partes, quarum est conspectus illustrior;sapientiae, illi propter spem vivere.Et quod est munus, quod opus sapientiae? Non modo carum sibi quemque, verum etiam vehementer carum esse? Tu</p>
  </div>
</section>

<section class="connect">
  <h2 class="col-title" style="left:71px;top:68px">Newsletter</h2>
  <svg class="abs" style="left:300px;top:112px" width="120" height="20" viewBox="0 0 140 20" fill="none" stroke="#333" stroke-dasharray="2 3"><path d="M2 10c30-8 60 10 95 2 12-3 20-5 30-5"/></svg>
  <p class="col-copy" style="left:71px;top:152px">Quia nec honesto quic quam honestius nec turpi turpius. Tria<br>genera bonorum; Quid iudicant sensus</p>
  <div class="abs email">Email Address</div>
  <div class="btn subscribe">Subscribe</div>

  <h2 class="col-title" style="left:618px;top:68px">Contact Us</h2>
  <svg class="abs" style="left:840px;top:112px" width="120" height="20" viewBox="0 0 140 20" fill="none" stroke="#333" stroke-dasharray="2 3"><path d="M2 10c30-8 60 10 95 2 12-3 20-5 30-5"/></svg>
  <p class="col-copy" style="left:618px;top:152px;line-height:20px">Rimu Vale Honey Co Ltd 12 Kowhai Road, Taranaki 4310<br>Call Us: 06-555-0142<br>Mail To: hello@rimuvalehoney.co.nz</p>
  <div class="social"><i></i><i></i><i></i><i></i><i></i></div>
</section>

<footer class="footer">
  <div class="abs foot-brand"><span class="brand-mark"></span><span class="brand-name">RIMU VALE HONEY</span></div>
  <p class="abs foot-about">quaerimus, qualis Q. Nam quibus rebus efficiuntur voluptates, eae non sunt in potestate sapientis. Negare non possum. Huic mori optimum esse propter desperationem sapientiae.</p>
  <div class="btn foot-btn">Read More</div>

  <div class="foot-rule" style="left:357px"></div>
  <h3 class="foot-head" style="left:390px">QUICK LINK</h3>
  <ul class="foot-list" style="left:395px"><li>Home</li><li>Shop</li><li>About Us</li><li>Our Product</li><li>Testimonial</li><li>Contact Us</li></ul>

  <div class="foot-rule" style="left:535px"></div>
  <h3 class="foot-head" style="left:578px">CONTACT US</h3>
  <div class="foot-contact">
    <div><svg width="12" height="14" viewBox="0 0 12 14" fill="#f9ab00"><path d="M6 0a5 5 0 0 0-5 5c0 4 5 9 5 9s5-5 5-9a5 5 0 0 0-5-5zm0 7a2 2 0 1 1 0-4 2 2 0 0 1 0 4z"/></svg><span>Rimu Vale Honey Co Ltd<br>12 Kowhai Road<br>Taranaki 4310</span></div>
    <div style="margin-top:14px"><svg width="12" height="12" viewBox="0 0 12 12" fill="#f9ab00"><path d="M2 0h3l1 3-2 1a7 7 0 0 0 4 4l1-2 3 1v3a2 2 0 0 1-2 2A10 10 0 0 1 0 2a2 2 0 0 1 2-2z"/></svg><span>06-555-0142</span></div>
    <div style="margin-top:-6px"><svg width="12" height="10" viewBox="0 0 12 10" fill="#f9ab00"><path d="M0 0h12v10H0zM1 1l5 4 5-4"/></svg><span>hello@rimuvalehoney.co.nz</span></div>
    <div style="margin-top:-6px"><svg width="12" height="12" viewBox="0 0 12 12" fill="none" stroke="#f9ab00"><circle cx="6" cy="6" r="5"/><path d="M1 6h10M6 1c3 3 3 7 0 10M6 1c-3 3-3 7 0 10"/></svg><span>www.rimuvalehoney.co.nz</span></div>
  </div>

  <div class="foot-rule" style="left:788px"></div>
  <h3 class="foot-head" style="left:835px">OUR BLOGS</h3>
  <div class="foot-post" style="top:128px"><div class="thumb" role="img" aria-label="Honey jar thumbnail"></div><div><h4>An hoc usque quaque,<br>aliter in vita? Non igitur de</h4><small>April 19, 2020</small></div></div>
  <div class="foot-post" style="top:208px"><div class="thumb" role="img" aria-label="Honey dipper thumbnail"></div><div><h4>An hoc usque quaque,<br>aliter in vita? Non igitur de</h4><small>March 19, 2020</small></div></div>
</footer>

<div class="abs copyright" style="left:0;width:1200px">Copyright © 2021, Rimu Vale Honey Co, All Right Reserved
  <div class="mini-social"><i></i><i></i><i></i><i></i><i></i></div>
</div>

</body>
</html>
```